Business card for medical clinic

I need an upmarket, modern medical/health business card for my clinic

Contact Information for Business Card

name, address, email, qr code

```html
<!DOCTYPE html>
<html lang="en">
<head>
<meta charset="utf-8">
<title>Calder Health Partners – Business Card</title>
<link rel="stylesheet" href="https://fonts.googleapis.com/css2?family=Montserrat:wght@400;500;700&display=swap">
<style>
  :root {
    --page: #d9d4ce;
    --card: #ece7e1;
    --ink-dark: #141414;
    --teal: #1f8fa5;
    --teal-deep: #136f84;
    --text: #2a2a2a;
    --text-soft: #3d3d3d;
  }
  html, body {
    margin: 0;
    width: 1200px;
    height: 1047px;
    overflow: hidden;
    background: var(--page);
    font-family: "Montserrat", sans-serif;
  }
  .business-card {
    position: absolute;
    left: 80px;
    top: 240px;
    width: 1040px;
    height: 568px;
    border-radius: 28px;
    overflow: hidden;
    background: var(--card);
    box-shadow: 0 10px 30px rgba(0,0,0,0.15);
  }
  .header-band {
    position: absolute;
    left: 0;
    top: 0;
    width: 1040px;
    height: 230px;
    background: linear-gradient(180deg, var(--ink-dark) 0%, var(--ink-dark) 62%, var(--teal-deep) 100%);
  }
  .brand {
    position: absolute;
    left: 590px;
    top: 82px;
    display: flex;
    align-items: center;
    gap: 16px;
  }
  .brand-dot {
    width: 34px; height: 34px;
    border-radius: 50%;
    background: var(--teal);
  }
  .brand-name {
    margin: 0;
    color: var(--teal);
    font-weight: 500;
    font-size: 34px;
    line-height: 1.15;
    letter-spacing: 1px;
  }
  .person {
    position: absolute;
    left: 0;
    top: 283px;
    padding-left: 40px;
    border-left: 26px solid var(--teal);
  }
  .person-name {
    margin: 0 0 0 -26px;
    font-weight: 700;
    font-size: 36px;
    letter-spacing: 1px;
    color: var(--teal);
    line-height: 1;
  }
  .person-role {
    margin: 12px 0 0 -26px;
    font-size: 26px;
    color: var(--text-soft);
  }
  .contact-list {
    position: absolute;
    left: 38px;
    top: 418px;
    margin: 0; padding: 0;
    list-style: none;
    font-size: 26px;
    color: var(--text);
  }
  .contact-list li {
    display: flex;
    align-items: center;
    gap: 10px;
    height: 40px;
  }
  .contact-icon { width: 22px; height: 22px; fill: var(--text-soft); }
  .address {
    position: absolute;
    right: 34px;
    top: 460px;
    margin: 0;
    text-align: right;
    font-style: normal;
    font-size: 26px;
    line-height: 40px;
    color: var(--text);
  }
</style>
</head>
<body>
  <article class="business-card">
    <div class="header-band" role="img" aria-label="Decorative dark header with a teal wave band"></div>

    <div class="brand">
      <span class="brand-dot"></span>
      <p class="brand-name">CALDER HEALTH<br>PARTNERS</p>
    </div>

    <div class="person">
      <h1 class="person-name">DANIEL CARTER</h1>
      <p class="person-role">Managing Director</p>
    </div>

    <ul class="contact-list">
      <li>
        <svg class="contact-icon" viewBox="0 0 24 24"><path d="M6.6 10.8a15.2 15.2 0 0 0 6.6 6.6l2.2-2.2a1 1 0 0 1 1-.25 11.4 11.4 0 0 0 3.6.57 1 1 0 0 1 1 1V20a1 1 0 0 1-1 1A17 17 0 0 1 3 4a1 1 0 0 1 1-1h3.5a1 1 0 0 1 1 1c0 1.25.2 2.45.57 3.6a1 1 0 0 1-.25 1z"/></svg>
        123 456 789
      </li>
      <li>
        <svg class="contact-icon" viewBox="0 0 24 24"><path d="M2 6h20v12H2z M4 8v.4l8 5 8-5V8l-8 5z" fill-rule="evenodd"/></svg>
        info@yourmail.com
      </li>
      <li>
        <svg class="contact-icon" viewBox="0 0 24 24"><circle cx="12" cy="12" r="10"/><path d="M2 12h20M12 2c3 3 3 17 0 20M12 2c-3 3-3 17 0 20" stroke="#ece7e1" stroke-width="1.5" fill="none"/></svg>
        www.yourwebsite.com
      </li>
    </ul>

    <address class="address">Your address, City<br>State, Zip 1234</address>
  </article>
</body>
</html>
```